Meridale Partners Website

Meridale Partners (MP) provide Analytics & Enterprise Performance Management (EPM) advisory & consultancy services. We are passionate about data and making a difference for our clients by working in partnership with them, helping them on their journey to becoming an Meridale Partner. We deliver insights which give our clients a competitive edge and a much deeper understanding of their organisation.

We need a website which shows who we are, what we do and how we do it.

www.meridale-partners.example is our very basic website at the moment. We want to completely revamp it with a corporate look

```html
<!DOCTYPE html>
<html lang="en">
<head>
<meta charset="utf-8">
<title>Meridale Partners – Data Analytics &amp; EPM Consulting</title>
<link rel="stylesheet" href="https://fonts.googleapis.com/css2?family=Poppins:wght@400;500;600;700;800&display=swap">
<style>
:root{
  --orange:#f7941d;
  --orange-soft:#fba33f;
  --navy:#2b5673;
  --navy-deep:#244a64;
  --ink:#333333;
  --text:#444444;
  --grey-bg:#ebebeb;
  --white:#ffffff;
}
*{margin:0;padding:0;box-sizing:border-box}
html,body{width:1200px;height:2677px;overflow:hidden}
body{position:relative;background:var(--white);font-family:"Poppins",sans-serif;color:var(--text)}
h1,h2{font-weight:400}

/* header */
.site-header{position:absolute;left:0;top:0;width:1200px;height:94px;background:var(--white)}
.brand{position:absolute;display:flex;align-items:center;gap:12px}
.brand-mark{width:40px;height:40px;border-radius:50%;border:7px solid var(--navy)}
.brand-name{font-weight:600;color:var(--navy);font-size:19px;line-height:21px;letter-spacing:.5px;text-transform:uppercase}
.site-header .brand{left:145px;top:23px}
.main-nav{position:absolute;top:38px;left:0;width:1200px;font-size:13.5px;font-weight:500;color:#111}
.main-nav a{position:absolute;color:inherit;text-decoration:none;white-space:nowrap}
.main-nav a.active{color:var(--orange)}
.main-nav a.active::after{content:"";position:absolute;left:0;right:0;bottom:-5px;height:2px;background:var(--orange)}
.social-dot{position:absolute;top:34px;width:25px;height:25px;border-radius:50%;background:var(--orange)}

/* hero */
.hero{position:absolute;left:0;top:94px;width:1200px;height:511px;background:linear-gradient(100deg,#3f6384 0%,#2e5273 40%,#566f80 65%,#7b7f7c 85%,#5d6c78 100%)}
.hero-title{position:absolute;left:0;width:1200px;top:236px;text-align:center;font-weight:800;font-size:58px;color:var(--white);letter-spacing:.5px}
.hero-sub{position:absolute;left:0;width:1200px;top:326px;text-align:center;font-weight:600;font-size:22px;color:var(--white)}
.btn-hero{position:absolute;left:480px;top:397px;width:204px;height:51px;border-radius:26px;background:var(--orange);color:var(--white);font-weight:500;font-size:17px;display:flex;align-items:center;justify-content:center;letter-spacing:.5px}

/* section headings */
.section-title{position:absolute;font-size:41px;color:var(--ink);font-weight:400;white-space:nowrap;line-height:1}
.section-title strong{font-weight:700;position:relative;display:inline-block}
.section-title strong::after{content:"";position:absolute;left:0;right:0;bottom:-10px;height:3px;background:var(--ink)}

/* who */
.who-accent{position:absolute;left:138px;top:728px;width:21px;height:327px;background:var(--orange-soft)}
.who-photo{position:absolute;left:159px;top:698px;width:326px;height:387px;background:linear-gradient(120deg,#d9dee2,#8e9196 55%,#3d3f44)}
.who-text{position:absolute;left:522px;top:765px;width:548px;font-size:15.5px;line-height:32.5px;color:#333}
.btn-small{position:absolute;background:var(--orange);color:var(--white);font-size:14px;border-radius:4px;display:flex;align-items:center;justify-content:center}

/* how */
.how{position:absolute;left:0;top:1200px;width:1200px;height:655px;background:var(--grey-bg)}
.how-photo{position:absolute;left:33px;top:1267px;width:618px;height:497px;border:2px solid var(--orange);border-bottom-right-radius:75px;background:linear-gradient(135deg,#e9e6e2,#c9c5c0 45%,#6f7a86 75%,#2f3a48)}
.how-card{position:absolute;left:600px;top:1365px;width:477px;height:268px;background:var(--white);border-top-left-radius:62px;padding:32px 22px 0 40px;text-align:center;font-size:15.5px;line-height:29px;color:#333}

.orange-rule{position:absolute;left:0;top:1855px;width:1200px;height:8px;background:var(--orange)}

/* connect */
.connect{position:absolute;left:0;top:1863px;width:610px;height:467px;background:var(--grey-bg)}
.connect-title{position:absolute;left:0;width:625px;top:1887px;text-align:center;font-size:41px;font-weight:400;color:var(--ink)}
.connect-title strong{font-weight:700}
.connect-sub{position:absolute;left:0;width:618px;top:1942px;text-align:center;font-size:17px;color:var(--orange);font-weight:500;letter-spacing:.3px}
.field{position:absolute;background:var(--white);border-radius:10px;font-size:11px;color:#333;padding:15px 16px}
.what{position:absolute;left:610px;top:1863px;width:590px;height:467px;background:linear-gradient(120deg,#3c6585,#2f5b7b 50%,#385f7c)}
.what-title{position:absolute;left:610px;width:532px;top:1918px;text-align:center;font-size:41px;font-weight:400;color:var(--white)}
.what-title strong{font-weight:700;position:relative}
.what-title strong::after{content:"";position:absolute;left:0;right:0;bottom:-8px;height:3px;background:var(--white)}
.what-text{position:absolute;left:670px;width:422px;top:1988px;text-align:center;font-size:19.5px;line-height:35px;color:var(--white)}
.btn-outline{position:absolute;left:814px;top:2207px;width:150px;height:28px;background:var(--white);color:var(--navy);font-weight:600;font-size:17px;display:flex;align-items:center;justify-content:center;border-radius:2px}

/* footer */
.site-footer{position:absolute;left:0;top:2330px;width:1200px;height:347px;background:var(--navy)}
.footer-brand{left:502px;top:2373px}
.footer-brand .brand-mark{border-color:var(--white);width:48px;height:48px}
.footer-brand .brand-name{color:var(--white);font-size:18px;font-weight:600}
.foot-head{position:absolute;top:2492px;font-size:15px;font-weight:600;color:var(--white);letter-spacing:.3px;display:flex;align-items:center;gap:10px}
.foot-line{position:absolute;font-size:12px;font-weight:500;color:var(--white);display:flex;align-items:center;gap:10px;white-space:nowrap}
.foot-line svg{flex:none}
.news-input{position:absolute;left:779px;top:2523px;width:280px;height:37px;background:var(--white);border-radius:8px;font-size:12px;color:#333;padding:10px 11px}
.copyright{position:absolute;left:0;width:1200px;top:2631px;text-align:center;font-size:12.5px;font-weight:500;color:var(--white)}
</style>
</head>
<body>

<header class="site-header">
  <div class="brand"><span class="brand-mark"></span><span class="brand-name">Meridale<br>Partners</span></div>
  <nav class="main-nav">
    <a class="active" style="left:581px">HOME</a>
    <a style="left:690px">SERVICES</a>
    <a style="left:823px">ABOUT US</a>
    <a style="left:960px">CONTACT US</a>
  </nav>
  <span class="social-dot" style="left:1082px"></span>
  <span class="social-dot" style="left:1127px"></span>
</header>

<section class="hero" role="img" aria-label="Photo of a business team meeting around a conference table, tinted blue"></section>
<h1 class="hero-title">MERIDALE PARTNERS.</h1>
<p class="hero-sub">DATA ANALYTICS &amp; EPM CONSULTING SERVICES</p>
<a class="btn-hero">GET STARTED</a>

<!-- who we are -->
<div class="who-accent"></div>
<div class="who-photo" role="img" aria-label="Portrait photo of a smiling consultant in a grey suit"></div>
<h2 class="section-title" style="left:522px;top:702px"><strong>Who</strong> We Are ?</h2>
<p class="who-text">Lorem Ipsum is simply dummy text of the printing and typesetting industry. Lorem Ipsum has been the industry's standard dummy text ever since the 1500s, when an unknown printer took a galley of type and scrambled it to make a type specimen book. It has survived not only five centuries, but also the leap into electronic typesetting, remaining essentially unchanged. It was popularised in the 1960s with the release of Brightform sheets containing Lorem Ipsum passages, and more recently with desktop publishing software like Pressly Layout including versions of Lorem Ipsum.</p>
<a class="btn-small" style="left:522px;top:1076px;width:98px;height:24px">Read More</a>

<!-- how we do -->
<section class="how"></section>
<div class="how-photo" role="img" aria-label="Photo of two colleagues reviewing printed charts at a desk with a laptop"></div>
<h2 class="section-title" style="left:706px;top:1285px"><strong>How</strong> We Do ?</h2>
<p class="how-card">It is a long established fact that a reader will be distracted by the readable content of a page when looking at its layout. The point of using Lorem that it has a more-or-less normal distribution of letters, as opposed to using 'Content here, content here', making it look like readable English. Many desktop publishing packages and web page .</p>

<div class="orange-rule"></div>

<!-- connect -->
<section class="connect"></section>
<h2 class="connect-title"><strong>Lets</strong> Connect</h2>
<p class="connect-sub">TO DISCUSS YOUR BUSINESS NEEDS</p>
<div class="field" style="left:113px;top:1997px;width:196px;height:41px">First Name</div>
<div class="field" style="left:329px;top:1996px;width:196px;height:41px;padding-top:13px">Last Name</div>
<div class="field" style="left:112px;top:2063px;width:413px;height:41px">Phone No</div>
<div class="field" style="left:111px;top:2124px;width:413px;height:122px;padding-top:16px;padding-left:20px">Message</div>
<a class="btn-small" style="left:247px;top:2272px;width:101px;height:24px">Submit</a>

<section class="what" role="img" aria-label="Blue tinted photo of hands over a desk"></section>
<h2 class="what-title"><strong>What</strong> We Do ?</h2>
<p class="what-text">MP are a Data Analytics &amp; EPM company, specialising in the implementation and support of Business Intelligence, EPM and Data Analytics business solutions, both in of the Cloud so&nbsp; it and on-premise.</p>
<a class="btn-outline">See Our Work</a>

<!-- footer -->
<footer class="site-footer"></footer>
<div class="brand footer-brand"><span class="brand-mark"></span><span class="brand-name">Meridale<br>Partners</span></div>

<div class="foot-head" style="left:174px">CONTACT US</div>
<div class="foot-line" style="left:152px;top:2527px">
  <svg width="11" height="8" viewBox="0 0 11 8"><rect x=".5" y=".5" width="10" height="7" fill="none" stroke="#fff"/><path d="M.5 .5 5.5 4.5 10.5 .5" fill="none" stroke="#fff"/></svg>
  INFO@MERIDALE-PARTNERS.EXAMPLE</div>
<div class="foot-line" style="left:152px;top:2559px">
  <svg width="12" height="12" viewBox="0 0 24 24"><path fill="#fff" d="M6.6 10.8a15 15 0 0 0 6.6 6.6l2.2-2.2a1 1 0 0 1 1-.25 11.4 11.4 0 0 0 3.6.57 1 1 0 0 1 1 1V20a1 1 0 0 1-1 1A17 17 0 0 1 3 4a1 1 0 0 1 1-1h3.5a1 1 0 0 1 1 1c0 1.25.2 2.45.57 3.570a1 1 0 0 1-.25 1z"/></svg>
  01 555 0142</div>

<div class="foot-head" style="left:496px">VISIT US</div>
<div class="foot-line" style="left:473px;top:2528px">
  <svg width="10" height="13" viewBox="0 0 10 13"><path fill="#fff" d="M5 0a5 5 0 0 0-5 5c0 3.7 5 8 5 8s5-4.3 5-8a5 5 0 0 0-5-5zm0 7a2 2 0 1 1 0-4 2 2 0 0 1 0 4z"/></svg>
  14 HARBOUR LANE,</div>
<div class="foot-line" style="left:496px;top:2560px">WESTFIELD QUARTER, DUBLIN 8, D08 QX41</div>

<div class="foot-head" style="left:787px">SUBSCRIBE FOR NEWSLETTER
  <svg width="24" height="22" viewBox="0 0 24 22"><path d="M1 10 23 1 18 21 11 14 23 1M11 14v6l3-4" fill="none" stroke="#fff" stroke-width="1.6" stroke-linejoin="round"/></svg>
</div>
<div class="news-input">Your Email Address</div>

<p class="copyright">© copyrights 2022 Meridale Partners |&nbsp; All Rights Reserved</p>

</body>
</html>
```